Electrician Business Card/ company logo/small business

New Business Cards and logo needed that will catch peoples eye and say we went that extra step. Attached is a design possibly to be incorporated, if u have your own great, lets see it!... This will be a small local business. thank you for all you do!
Halvern Electric
Ned Fosky Owner
Journeyman Electrician
phone 1.555.208.3471
email: KQLHalvernElectric@quellmail.net
call for free estimate!
Updates

Accepted and approved for cards

Target Market(s)

support small local business

Industry/Entity Type

Electrical,

Contact Information for Business Card

name, title,company/ logo, phone, email, free estimate

Other font styles liked:
• easy to read

Colors

Designer to choose colors to be used in the design.

Requirements
Must have
• eye catching everything! logo and halvern electric listed on business card/logo, incorp logo in the background of card
Nice to have
• lightening bolts in eyes or around the triangle? vertical, modern, any design that would be unique and stand out
Should not have
• pinks, reds, yellows,brown

```html
<!DOCTYPE html>
<html lang="en">
<head>
<meta charset="utf-8">
<title>Halvern Electric — Business Card</title>
<link href="https://fonts.googleapis.com/css2?family=Arimo:wght@400;700&display=swap" rel="stylesheet">
<style>
  :root {
    --bg: #e9ebee;
    --blue-deep: #0a5db3;
    --blue-mid: #0a7cc8;
    --blue-bright: #0b94d8;
    --ink: #1d1d1f;
    --white: #ffffff;
    --rule: #cfd3d8;
  }
  * { box-sizing: border-box; margin: 0; padding: 0; }
  html, body {
    width: 1200px; height: 1015px; overflow: hidden;
    background: var(--bg);
    font-family: "Arimo", Arial, sans-serif;
  }
  .sheet {
    width: 1200px; height: 1015px;
    display: flex; flex-direction: column; align-items: center; justify-content: center;
    gap: 40px;
  }
  .card {
    width: 800px; height: 457px;
    position: relative; overflow: hidden;
    box-shadow: 0 10px 30px rgba(0,0,0,.18);
  }

  /* Front */
  .card--front {
    background: linear-gradient(160deg, var(--blue-deep) 0%, var(--blue-mid) 50%, var(--blue-bright) 100%);
    display: flex; align-items: center; justify-content: center;
  }
  .brand {
    display: flex; align-items: center; gap: 22px;
    font-weight: 700; text-transform: uppercase; letter-spacing: .06em;
  }
  .brand__dot { border-radius: 50%; flex: none; }
  .card--front .brand { color: var(--white); font-size: 46px; }
  .card--front .brand__dot { width: 64px; height: 64px; background: var(--white); }

  /* Back */
  .card--back { background: var(--white); display: flex; }
  .back__brand {
    width: 350px; display: flex; align-items: center; justify-content: center;
  }
  .back__brand .brand {
    flex-direction: column; gap: 16px; text-align: center;
    color: var(--blue-mid); font-size: 30px; line-height: 1.15;
  }
  .back__brand .brand__dot { width: 70px; height: 70px; background: var(--blue-mid); }
  .back__rule {
    width: 1px; margin: 70px 0;
    background: linear-gradient(to bottom, transparent, var(--rule) 20%, var(--rule) 80%, transparent);
  }
  .contact {
    flex: 1; padding: 0 40px 0 50px;
    display: flex; flex-direction: column; justify-content: center;
  }
  .contact__name {
    font-size: 38px; font-weight: 700; letter-spacing: .01em;
    color: var(--blue-deep); text-transform: uppercase; line-height: 1;
  }
  .contact__title { font-size: 21px; color: var(--ink); margin-top: 6px; }
  .contact__list { list-style: none; margin-top: 34px; }
  .contact__item {
    display: flex; align-items: center; gap: 14px;
    font-size: 19px; color: var(--ink); line-height: 1.55;
  }
  .contact__icon { width: 20px; height: 20px; flex: none; fill: var(--blue-mid); }
  .contact__accent { color: var(--blue-bright); }
</style>
</head>
<body>
<main class="sheet">
  <section class="card card--front" aria-label="Card front">
    <div class="brand">
      <span class="brand__dot"></span>
      <span>Halvern Electric</span>
    </div>
  </section>

  <section class="card card--back" aria-label="Card back">
    <div class="back__brand">
      <div class="brand">
        <span class="brand__dot"></span>
        <span>Halvern<br>Electric</span>
      </div>
    </div>
    <div class="back__rule"></div>
    <div class="contact">
      <h1 class="contact__name">Ned Fosky</h1>
      <p class="contact__title">Journeyman Electrician</p>
      <ul class="contact__list">
        <li class="contact__item">
          <svg class="contact__icon" viewBox="0 0 24 24" aria-hidden="true"><path d="M6.6 10.8a15.1 15.1 0 0 0 6.6 6.6l2.2-2.2c.3-.3.7-.4 1-.2 1.1.4 2.3.6 3.6.6.6 0 1 .4 1 1V20c0 .6-.4 1-1 1A17 17 0 0 1 3 4c0-.6.4-1 1-1h3.5c.6 0 1 .4 1 1 0 1.3.2 2.5.6 3.6.1.3 0 .7-.2 1z"/></svg>
          <span>1.555.208.3471</span>
        </li>
        <li class="contact__item">
          <svg class="contact__icon" viewBox="0 0 24 24" aria-hidden="true"><path d="M2 5h20v14H2z M2 5l10 8 10-8" fill="none" stroke="currentColor"/><path d="M2 5h20l-10 8z"/><path d="M2 7v12h20V7l-10 8z"/></svg>
          <span>KQLHalvernElectric@quellmail.net</span>
        </li>
        <li class="contact__item">
          <svg class="contact__icon" viewBox="0 0 24 24" aria-hidden="true"><circle cx="12" cy="12" r="9.5" fill="none" stroke="#0a7cc8" stroke-width="2"/><ellipse cx="12" cy="12" rx="4" ry="9.5" fill="none" stroke="#0a7cc8" stroke-width="1.6"/><path d="M2.5 12h19M4 7h16M4 17h16" stroke="#0a7cc8" stroke-width="1.4"/></svg>
          <span>www.<span class="contact__accent">halvernelectric</span>.com</span>
        </li>
      </ul>
    </div>
  </section>
</main>
</body>
</html>
```